Progressive Flow Chart

Looking for a progressive flow chart centered and branching off. They all build on each other 1-3. There will be 3 different pages.

Target Market(s)

Business Owners - High Net worth Individuals

Industry/Entity Type

Finance & Business Consulting

Font styles to use
Serif

Colors
0054AA
0677BA
7BADD7
CADEEF
E8F1F8
0094D4
00A9DD
6FCCEA
C7EBF8
E9F6FB
00AB8E
00BBA5
67D7C9
C6EFE9
E9F9F6

Requirements
Nice to have
• Clean, simple, and approachable.
Should not have
• Very Busy

```html
<!DOCTYPE html>
<html lang="en">
<head>
<meta charset="utf-8">
<title>Living Trust Flow Chart</title>
<link rel="stylesheet" href="https://fonts.googleapis.com/css2?family=Nunito+Sans:wght@400;700;800;900&display=swap">
<style>
  :root {
    --page: #fbf6f5;
    --navy: #0d1538;
    --navy-deep: #121a4d;
    --teal: #1de3b5;
    --teal-soft: #67d7c9;
    --sky: #6fcbea;
    --mint: #8ff5d8;
    --white: #ffffff;
    --line-inner: #d9f5ee;
    --brand: #39b8d8;
  }
  html, body {
    margin: 0;
    width: 1200px;
    height: 1200px;
    overflow: hidden;
    background: var(--page);
  }
  .canvas {
    position: relative;
    width: 1200px;
    height: 1200px;
    display: flex;
    align-items: center;
    justify-content: center;
  }
  .chart {
    display: block;
    width: 1200px;
    height: 849px;
    font-family: "Nunito Sans", "Avenir Next", sans-serif;
  }
  .card-bg { fill: var(--navy); }
  .box-outer { fill: none; stroke: var(--teal); stroke-width: 3; }
  .box-inner { fill: var(--navy); stroke: var(--line-inner); stroke-width: 1.5; }
  .box-tab { fill: url(#tabGradient); }
  .tab-icon { fill: none; stroke: var(--navy); stroke-width: 3; stroke-linecap: round; stroke-linejoin: round; }
  .tab-icon-fill { fill: var(--navy); }
  .box-title { fill: var(--white); font-weight: 900; font-size: 31px; text-anchor: middle; }
  .box-sub { fill: var(--white); font-weight: 400; font-size: 14.5px; text-anchor: middle; }
  .flow { fill: none; stroke: var(--teal); stroke-width: 3; }
  .arrowhead { fill: var(--sky); }
  .pill { fill: var(--teal); }
  .pill-text { fill: var(--navy); font-weight: 900; font-size: 15px; text-anchor: middle; dominant-baseline: central; letter-spacing: 0.5px; }
  .ring { fill: url(#ringGradient); stroke: var(--teal); stroke-width: 3; }
  .ring-core { fill: var(--navy); stroke: var(--navy-deep); stroke-width: 12; }
  .ring-label { fill: var(--navy); font-weight: 900; font-size: 44px; letter-spacing: 4px; }
  .core-text { fill: var(--white); font-weight: 900; font-size: 33px; text-anchor: middle; }
  .brand-name { fill: var(--brand); font-weight: 800; font-size: 34px; text-anchor: middle; letter-spacing: 1px; }
  .brand-line { fill: var(--brand); font-weight: 400; font-size: 14px; text-anchor: middle; letter-spacing: 4px; }
  .brand-dot { fill: var(--teal); }
</style>
</head>
<body>
<main class="canvas">
  <svg class="chart" viewBox="0 0 1300 920" xmlns="http://www.w3.org/2000/svg" aria-label="Living trust flow chart">
    <defs>
      <linearGradient id="tabGradient" x1="0" y1="0" x2="1" y2="1">
        <stop offset="0" stop-color="#1de3b5"/>
        <stop offset="1" stop-color="#00bba5"/>
      </linearGradient>
      <linearGradient id="ringGradient" x1="0" y1="0" x2="0" y2="1">
        <stop offset="0" stop-color="#ffffff"/>
        <stop offset="0.5" stop-color="#e9f9f6"/>
        <stop offset="1" stop-color="#7ff2cf"/>
      </linearGradient>
      <marker id="head" viewBox="0 0 12 12" refX="10" refY="6" markerWidth="7" markerHeight="7" orient="auto-start-reverse">
        <path class="arrowhead" d="M0 0 L12 6 L0 12 Z"/>
      </marker>
      <path id="ringArc" d="M 607.3 500.2 A 138 138 0 1 1 866.7 500.2"/>
    </defs>

    <rect class="card-bg" x="0" y="0" width="1300" height="920"/>

    <!-- flow lines -->
    <g class="flows">
      <line class="flow" x1="545" y1="451" x2="388" y2="451" marker-end="url(#head)"/>
      <line class="flow" x1="180" y1="703" x2="180" y2="508" marker-end="url(#head)"/>
      <line class="flow" x1="276" y1="505" x2="276" y2="700" marker-end="url(#head)"/>
      <line class="flow" x1="325" y1="703" x2="560" y2="537" marker-end="url(#head)"/>
      <line class="flow" x1="370" y1="505" x2="533" y2="708" marker-end="url(#head)"/>
      <line class="flow" x1="513" y1="758" x2="388" y2="758" marker-end="url(#head)"/>
      <polyline class="flow" points="565,703 565,673 790,673 790,638" marker-end="url(#head)"/>
      <polyline class="flow" points="878,578 878,652 1075,652 1075,707" marker-end="url(#head)"/>
      <polyline class="flow" points="1100,703 1100,627 900,627 900,556" marker-end="url(#head)"/>
    </g>

    <!-- flow labels -->
    <g class="labels">
      <rect class="pill" x="428" y="441" width="82" height="20" rx="2"/>
      <text class="pill-text" x="469" y="451">INVEST</text>

      <g transform="translate(180 617) rotate(-90)">
        <rect class="pill" x="-45" y="-10" width="90" height="20" rx="2"/>
        <text class="pill-text" x="0" y="0">INTEREST</text>
      </g>
      <g transform="translate(276 598) rotate(-90)">
        <rect class="pill" x="-61" y="-10" width="122" height="20" rx="2"/>
        <text class="pill-text" x="0" y="0">INVESTMENT</text>
      </g>
      <g transform="translate(403 645) rotate(-35)">
        <rect class="pill" x="-42" y="-10" width="84" height="20" rx="2"/>
        <text class="pill-text" x="0" y="0">INCOME</text>
      </g>
      <rect class="pill" x="425" y="748" width="64" height="20" rx="2"/>
      <text class="pill-text" x="457" y="758">RENT</text>
      <rect class="pill" x="633" y="663" width="84" height="20" rx="2"/>
      <text class="pill-text" x="675" y="673">INCOME</text>
    </g>

    <!-- top row -->
    <g class="box box-crt" transform="translate(98 102)">
      <rect class="box-outer" width="287" height="110" rx="14"/>
      <rect class="box-inner" x="6" y="6" width="275" height="98" rx="10"/>
      <path class="box-tab" d="M6 16 A10 10 0 0 1 16 6 H66 V30 A36 36 0 0 1 30 66 H6 Z"/>
      <rect class="tab-icon" x="18" y="16" width="26" height="34"/>
      <path class="tab-icon" d="M24 24 V44 M31 24 V44 M38 24 V44"/>
      <text class="box-title" x="143" y="66">CRT</text>
    </g>

    <g class="box box-daf" transform="translate(543 102)">
      <rect class="box-outer" width="287" height="110" rx="14"/>
      <rect class="box-inner" x="6" y="6" width="275" height="98" rx="10"/>
      <path class="box-tab" d="M6 16 A10 10 0 0 1 16 6 H66 V30 A36 36 0 0 1 30 66 H6 Z"/>
      <path class="tab-icon-fill" d="M16 14 H34 L42 22 V52 H16 Z"/>
      <path d="M21 30 H37 M21 36 H37 M21 42 H37" stroke="#1de3b5" stroke-width="2"/>
      <text class="box-title" x="143" y="67">DAF</text>
    </g>

    <g class="box box-grats" transform="translate(928 102)">
      <rect class="box-outer" width="287" height="110" rx="14"/>
      <rect class="box-inner" x="6" y="6" width="275" height="98" rx="10"/>
      <path class="box-tab" d="M6 16 A10 10 0 0 1 16 6 H66 V30 A36 36 0 0 1 30 66 H6 Z"/>
      <rect class="tab-icon" x="16" y="18" width="30" height="30" rx="2"/>
      <rect class="tab-icon" x="22" y="34" width="18" height="8"/>
      <circle class="tab-icon-fill" cx="46" cy="18" r="7"/>
      <text class="box-title" x="150" y="46">GRATS'</text>
      <text class="box-title" x="150" y="86">IDGT'S</text>
    </g>

    <!-- bank -->
    <g class="box box-bank" transform="translate(98 393)">
      <rect class="box-outer" width="287" height="110" rx="14"/>
      <rect class="box-inner" x="6" y="6" width="275" height="98" rx="10"/>
      <path class="box-tab" d="M6 16 A10 10 0 0 1 16 6 H66 V30 A36 36 0 0 1 30 66 H6 Z"/>
      <path class="tab-icon-fill" d="M14 24 L32 14 L50 24 Z"/>
      <path class="tab-icon" d="M20 28 V42 M28 28 V42 M36 28 V42 M44 28 V42 M14 46 H50"/>
      <text class="box-title" x="166" y="48">BANK</text>
      <text class="box-sub" x="166" y="70">MAKES INVESTMENTS TO</text>
      <text class="box-sub" x="166" y="90">REAL ESTATE + BUSINESS</text>
    </g>

    <!-- real estate -->
    <g class="box box-realestate" transform="translate(98 703)">
      <rect class="box-outer" width="287" height="110" rx="14"/>
      <rect class="box-inner" x="6" y="6" width="275" height="98" rx="10"/>
      <path class="box-tab" d="M6 16 A10 10 0 0 1 16 6 H66 V30 A36 36 0 0 1 30 66 H6 Z"/>
      <path class="tab-icon-fill" d="M22 24 L32 14 L42 24 V34 H22 Z"/>
      <path class="tab-icon" d="M12 46 H24 L32 42 H46 L52 36"/>
      <text class="box-title" x="142" y="43">REAL</text>
      <text class="box-title" x="142" y="77">ESTATE</text>
      <text class="box-sub" x="142" y="97">LLC</text>
    </g>

    <!-- business -->
    <g class="box box-business" transform="translate(543 703)">
      <rect class="box-outer" width="287" height="110" rx="14"/>
      <rect class="box-inner" x="6" y="6" width="275" height="98" rx="10"/>
      <path class="box-tab" d="M6 16 A10 10 0 0 1 16 6 H66 V30 A36 36 0 0 1 30 66 H6 Z"/>
      <path class="tab-icon" d="M12 24 L20 22 L30 32 L38 26 L50 26 M20 22 L14 36 L26 42 M38 26 L48 38 L40 44"/>
      <text class="box-title" x="167" y="47">BUSINESS</text>
      <text class="box-sub" x="167" y="70">LLC-MEMBER/MANAGER</text>
      <text class="box-sub" x="167" y="90">CORP= PRESIDENT</text>
    </g>

    <!-- insurance -->
    <g class="box box-insurance" transform="translate(933 703)">
      <rect class="box-outer" width="287" height="110" rx="14"/>
      <rect class="box-inner" x="6" y="6" width="275" height="98" rx="10"/>
      <path class="box-tab" d="M6 16 A10 10 0 0 1 16 6 H66 V30 A36 36 0 0 1 30 66 H6 Z"/>
      <path class="tab-icon" d="M32 14 V28 M25 21 H39 M14 26 V44 H50 V26 M14 34 L24 40 M50 34 L40 40"/>
      <text class="box-title" x="168" y="70">INSURANCE</text>
    </g>

    <!-- living trust hub -->
    <g class="hub">
      <circle class="ring" cx="737" cy="453" r="192"/>
      <text class="ring-label">
        <textPath href="#ringArc" startOffset="50%" text-anchor="middle">LIVING TRUST</textPath>
      </text>
      <circle class="ring-core" cx="737" cy="453" r="106"/>
      <text class="core-text" x="733" y="444">YOU</text>
      <text class="core-text" x="737" y="484">TRUSTEE</text>
    </g>

    <!-- firm name -->
    <g class="brand">
      <circle class="brand-dot" cx="1101" cy="430" r="14"/>
      <text class="brand-name" x="1101" y="535">HARBOR RIDGE</text>
      <text class="brand-line" x="1101" y="565">WEALTH</text>
    </g>
  </svg>
</main>
</body>
</html>
```